Coastline Premier Retreats Business Card Design

Design a business card for Coastline Premier Retreats. Look at the website for colors and reference. Card should have logo, name, title, office number, mobile number, email, URL and a tagline like, "Luxury Hotel & Resort Email Marketing" (This might change).

https://www.coastlinepremierretreats.example

The rest I will leave up to your imagination.

Contact Information for Business Card

Logo, name, title, office number, mobile number, email, URL and a tagline like, "Luxury Hotel & Resort Email Marketing" (This might change).

```html
<!DOCTYPE html>
<html lang="en">
<head>
<meta charset="utf-8">
<title>Coastline Premier Retreats – Business Card</title>
<link href="https://fonts.googleapis.com/css2?family=Arimo:wght@400;700&display=swap" rel="stylesheet">
<style>
  :root {
    --orange: #e8731a;
    --ink: #2b2b2b;
    --paper: #f4f4f4;
    --night: #171717;
    --backdrop: #1e1e1e;
    --white: #f5f5f5;
  }
  * { margin: 0; padding: 0; box-sizing: border-box; }
  html, body { width: 1200px; height: 1059px; overflow: hidden; }
  body { background: var(--backdrop); font-family: "Arimo", Arial, sans-serif; position: relative; }

  .card { position: absolute; }
  .card-front { left: 256px; top: 89px; width: 688px; height: 391px; background: var(--paper); }
  .card-back { left: 253px; top: 546px; width: 694px; height: 395px; background: var(--night); }

  .frame { position: absolute; left: 22px; top: 22px; width: 644px; height: 336px;
    border: 2px solid var(--orange); border-bottom: none; }
  .frame-base { position: absolute; top: 356px; height: 2px; background: var(--orange); }
  .frame-base.left { left: 22px; width: 156px; }
  .frame-base.right { left: 512px; width: 154px; }
  .tagline { position: absolute; left: 178px; width: 334px; top: 346px; text-align: center;
    font-size: 17px; color: var(--ink); }

  .brand { position: absolute; display: flex; align-items: center; gap: 10px; }
  .brand-mark { width: 14px; height: 14px; background: var(--orange); flex: none; }
  .brand-name { font-weight: 700; letter-spacing: 1px; text-transform: uppercase; line-height: 1.15; }
  .card-front .brand { left: 52px; top: 172px; width: 290px; justify-content: center; }
  .card-front .brand-name { font-size: 20px; color: var(--ink); }
  .card-back .brand { left: 0; right: 0; top: 180px; justify-content: center; gap: 14px; }
  .card-back .brand-mark { width: 20px; height: 20px; }
  .card-back .brand-name { font-size: 30px; color: var(--white); letter-spacing: 2px; }

  .divider { position: absolute; left: 350px; top: 100px; width: 1px; height: 190px; background: var(--orange); }

  .details { position: absolute; left: 379px; top: 96px; color: var(--ink); }
  .person-name { font-size: 30px; font-weight: 700; color: var(--orange); line-height: 1; letter-spacing: 0.3px; }
  .person-title { font-size: 16px; margin-top: 3px; }
  .address { font-size: 16px; line-height: 21px; margin-top: 14px; }
  .contacts { list-style: none; margin-top: 10px; }
  .contacts li { display: flex; align-items: center; gap: 7px; font-size: 15px; line-height: 21.5px; }
  .contacts svg { width: 12px; height: 12px; flex: none; fill: var(--orange); }
</style>
</head>
<body>
  <section class="card card-front" aria-label="Business card front">
    <div class="frame"></div>
    <div class="frame-base left"></div>
    <div class="frame-base right"></div>
    <p class="tagline">Luxury Hotel &amp; Resort Email Marketing</p>

    <div class="brand">
      <span class="brand-mark"></span>
      <span class="brand-name">Coastline Premier<br>Retreats</span>
    </div>

    <div class="divider"></div>

    <div class="details">
      <h1 class="person-name">DANIEL ROSS</h1>
      <p class="person-title">CEO/Founder</p>
      <p class="address">PO Box, 48 Harbor Lane<br>Bayview, CA 90000</p>
      <ul class="contacts">
        <li><svg viewBox="0 0 12 12"><path d="M3 0h6a1 1 0 0 1 1 1v10a1 1 0 0 1-1 1H3a1 1 0 0 1-1-1V1a1 1 0 0 1 1-1zm.5 1.5v7.5h5V1.5zM6 9.6a.7.7 0 1 0 0 1.4.7.7 0 0 0 0-1.4z"/></svg>555.014.2200</li>
        <li><svg viewBox="0 0 12 12"><path d="M1 3.5C1 2 3 1.5 6 1.5s5 .5 5 2v1.5H8.5V3.8H3.5V5H1zM3 6h6l1.5 4.5h-9zm3 1a1.3 1.3 0 1 0 0 2.6A1.3 1.3 0 0 0 6 7z"/></svg>+34 600 000 412</li>
        <li><svg viewBox="0 0 12 12"><path d="M0 4.5 6 1l6 3.5V11H0zm1.2 1v4.3L4.6 7.6zm9.6 0L7.4 7.6l3.4 2.2zM1.8 10h8.4L6 7.3z"/></svg>info@coastlinepremierretreats.example</li>
        <li><svg viewBox="0 0 12 12"><path d="M6 0a6 6 0 1 1 0 12A6 6 0 0 1 6 0zM3 2.3A4.6 4.6 0 0 0 1.5 7L3.5 6l1 1.5L4 10a4.6 4.6 0 0 0 5.5-.4L8 8l.5-2 2 .2A4.6 4.6 0 0 0 8 1.8L7 3 5 2.8z"/></svg>www.coastlinepremierretreats.example</li>
      </ul>
    </div>
  </section>

  <section class="card card-back" aria-label="Business card back">
    <div class="brand">
      <span class="brand-mark"></span>
      <span class="brand-name">Coastline Premier Retreats</span>
    </div>
  </section>
</body>
</html>
```